brightwell - Property Management DL Card

I am after a savvy designer to cut through junk mail! so many real estate agents use flyers to promote themselves and their business and usually sales. We are a property management firm (residential) and we want to represent landlords that have existing investment properties and need a quality agent to represent them. Can you help?
DL size, will be printed and delivered to mailboxes. For a look at our website go to www.brightwellrs.com.au. Keep it simple and clutter free.
it is to be double sided - with one side to be simple and clear - just our website, logo and telephone number on the back.
attached is our logo and our telephone number is 1300 48 92 16
the above are 2 essential elements to be included + our email address: admin@brightwellrs.com.au
also attached are our transparent price list

Target Market(s)
property investors,
people that manage properties themselves
Industry/Entity Type
Property Management
- arial
Look and feel

```html
<!DOCTYPE html>
<html lang="en">
<head>
<meta charset="utf-8">
<title>brightwell – Property Management DL Card</title>
<link rel="stylesheet" href="https://fonts.googleapis.com/css2?family=Arimo:wght@400;700&display=swap">
<style>
  :root{
    --page:#ecebe8;
    --card:#ffffff;
    --ink:#111111;
    --grey:#8a8a8a;
    --photo-light:#f1e7d6;
    --photo-mid:#d8c6aa;
    --photo-dark:#9a8466;
    --white:#ffffff;
  }
  *{box-sizing:border-box;margin:0;padding:0}
  html,body{width:1200px;height:900px;overflow:hidden}
  body{background:var(--page);font-family:"Arimo",Arial,sans-serif;color:var(--ink);position:relative}

  .dl-card{position:absolute;left:40px;top:193px;width:1120px;height:513px;background:var(--card);overflow:hidden}

  .interior-photo{position:absolute;left:0;top:0;width:460px;height:513px;
    background:
      radial-gradient(ellipse at 30% 20%, var(--photo-light) 0%, transparent 60%),
      linear-gradient(160deg, var(--photo-light) 0%, var(--photo-mid) 55%, var(--photo-dark) 100%);}

  .card-shapes{position:absolute;left:0;top:0;width:1120px;height:513px}

  .brand-name{position:absolute;left:462px;top:10px;font-size:66px;font-weight:400;letter-spacing:-1px;color:var(--ink)}

  .call-box{position:absolute;left:799px;top:15px;width:321px;height:96px;background:var(--grey);color:var(--white);text-align:center;font-weight:700}
  .call-box .call-label{font-size:29px;line-height:1;padding-top:7px}
  .call-box .call-number{font-size:45px;line-height:1;margin-top:9px;letter-spacing:.5px}

  .headline{position:absolute;left:477px;top:121px;font-size:32px;font-weight:700;white-space:nowrap}
  .intro{position:absolute;left:489px;top:160px;width:600px;font-size:15.5px;line-height:20px;text-align:center}

  .choose{position:absolute;left:449px;top:229px;font-size:25px;font-weight:700;white-space:nowrap}

  .benefits{position:absolute;left:446px;top:278px;list-style:none}
  .benefits li{display:flex;align-items:center;height:17px;font-size:17px;white-space:nowrap;position:absolute;left:0}
  .benefits li svg{width:24px;height:14px;margin-right:3px;flex:none}

  .fees{position:absolute;left:760px;top:335px;width:346px;text-align:center;font-size:27px;line-height:34px;font-weight:700;
    text-shadow:0 0 3px var(--white),0 0 3px var(--white),2px 3px 4px rgba(0,0,0,.45)}

  .contact-bar{position:absolute;left:470px;top:473px;width:650px;height:40px;color:var(--white);font-size:20px;font-weight:700}
  .contact-item{display:flex;align-items:center;position:absolute;top:6px;white-space:nowrap}
  .contact-item svg{width:28px;height:28px;margin-right:7px;flex:none}
  .contact-email{left:24px}
  .contact-web{left:340px}
</style>
</head>
<body>
  <main class="dl-card">
    <div class="interior-photo" role="img" aria-label="Photo of a bright modern open-plan living and dining room with a cream sofa"></div>

    <svg class="card-shapes" viewBox="0 0 1120 513" aria-hidden="true">
      <path d="M382,0 C430,140 440,330 425,513 L1120,513 L1120,0 Z" fill="var(--grey)"/>
      <path d="M445,0 C458,140 455,330 452,473 L1120,473 L1120,0 Z" fill="var(--card)"/>
      <rect x="440" y="473" width="680" height="40" fill="var(--grey)"/>
    </svg>

    <div class="brand-name">brightwell</div>

    <div class="call-box">
      <div class="call-label">Call Us Today:</div>
      <div class="call-number">1300 48 92 16</div>
    </div>

    <h1 class="headline">We Specialise In Property Management</h1>
    <p class="intro">Are you a property owner, private landlord, Mum/Dad investor or developer looking for quality property management to represent you? brightwell is the company to contact!</p>

    <h2 class="choose">Choose brightwell for your property management</h2>

    <ul class="benefits">
      <li style="top:0"><svg viewBox="0 0 24 14"><path d="M1,1 L7,7 L1,13 L5,13 L11,7 L5,1Z M11,1 L17,7 L11,13 L15,13 L21,7 L15,1Z" fill="var(--ink)"/></svg>Professional Property Management</li>
      <li style="top:31px"><svg viewBox="0 0 24 14"><path d="M1,1 L7,7 L1,13 L5,13 L11,7 L5,1Z M11,1 L17,7 L11,13 L15,13 L21,7 L15,1Z" fill="var(--ink)"/></svg>Return on investment</li>
      <li style="top:64px"><svg viewBox="0 0 24 14"><path d="M1,1 L7,7 L1,13 L5,13 L11,7 L5,1Z M11,1 L17,7 L11,13 L15,13 L21,7 L15,1Z" fill="var(--ink)"/></svg>Stress free lifestyle</li>
      <li style="top:100px"><svg viewBox="0 0 24 14"><path d="M1,1 L7,7 L1,13 L5,13 L11,7 L5,1Z M11,1 L17,7 L11,13 L15,13 L21,7 L15,1Z" fill="var(--ink)"/></svg>Minimise vacancy periods</li>
      <li style="top:134px"><svg viewBox="0 0 24 14"><path d="M1,1 L7,7 L1,13 L5,13 L11,7 L5,1Z M11,1 L17,7 L11,13 L15,13 L21,7 L15,1Z" fill="var(--ink)"/></svg>Repairs and maintenance</li>
    </ul>

    <p class="fees">With Competitive Fees<br>For All Budgets</p>

    <footer class="contact-bar">
      <span class="contact-item contact-email">
        <svg viewBox="0 0 28 28" aria-hidden="true">
          <circle cx="14" cy="14" r="13" fill="var(--white)" stroke="var(--ink)" stroke-width="2"/>
          <rect x="7" y="9" width="14" height="10" fill="none" stroke="var(--ink)" stroke-width="1.6"/>
          <path d="M7,9 L14,15 L21,9" fill="none" stroke="var(--ink)" stroke-width="1.6"/>
        </svg>
        admin@brightwellrs.com.au
      </span>
      <span class="contact-item contact-web">
        <svg viewBox="0 0 28 28" aria-hidden="true">
          <circle cx="14" cy="14" r="13" fill="var(--ink)"/>
          <ellipse cx="14" cy="14" rx="6" ry="12" fill="none" stroke="var(--white)" stroke-width="1.3"/>
          <path d="M2,14 H26 M4,8 H24 M4,20 H24" stroke="var(--white)" stroke-width="1.3"/>
        </svg>
        www.brightwellrs.com.au
      </span>
    </footer>
  </main>
</body>
</html>
```